Business Card Design & Gift cards, Gift Cert, Donation Card

Retail Gift Store-in addition to Business Cards we'd like sequenced 2 sided Gift cards, Gift Certificate Cards, and Donation Cards.please see examples and email for clarificationlogos attached with examples-
Gift Card, Gift Certificate and Donation Card will all be same style just differant upper right title, with back side info as example.
business card, as example is single sided.
looking for additional ideas for layout

Industry/Entity Type

Business

Contact Information for Business Card

211 Newman St.East Tawas, MI 48730989.362.8730Office@BrewKrew.com

Requirements
Must have
• Blue as per example
• Logos provided
• like gradiant background

```html
<!DOCTYPE html>
<html lang="en">
<head>
<meta charset="utf-8">
<title>Tillow Marsh – Business Card &amp; Gift Card</title>
<link rel="stylesheet" href="https://fonts.googleapis.com/css2?family=Comic+Neue:wght@400;700&family=Ubuntu:wght@400;500&display=swap">
<style>
  :root {
    --backdrop: #5b5b5b;
    --card: #ffffff;
    --ink: #111111;
    --ink-soft: #555555;
    --band: #000000;
    --band-text: #ffffff;
    --rule: #444444;
    --brand-blue: #2323c8;
    --sun-yellow: #f4d81c;
    --radius: 25px;
  }
  * { box-sizing: border-box; margin: 0; padding: 0; }
  html, body {
    width: 1105px; height: 1200px; overflow: hidden;
    background: var(--backdrop);
  }
  .canvas { position: relative; width: 1105px; height: 1200px; }

  .card {
    position: absolute; left: 196px; width: 720px; height: 411px;
    background: var(--card); border-radius: var(--radius); overflow: hidden;
  }
  .business-card { top: 146px; }
  .gift-card { top: 602px; }

  .brand-name {
    position: absolute; top: 60px; left: 0; width: 100%;
    text-align: center; font-family: "Comic Neue", cursive;
    font-weight: 400; font-size: 72px; letter-spacing: 2px; color: var(--ink);
  }
  .contact {
    position: absolute; top: 207px; left: 0; width: 100%;
    text-align: center; font-family: "Ubuntu", sans-serif;
    font-size: 21px; line-height: 30.5px; color: var(--ink-soft);
  }
  .contact b { color: var(--ink); font-weight: 500; }

  .offer-band {
    position: absolute; left: 0; top: 336px; width: 100%; height: 75px;
    background: var(--band); border-radius: 35px 35px 0 0;
    color: var(--band-text); font-family: "Comic Neue", cursive;
    font-size: 22px; line-height: 27px; text-align: center; padding-top: 9px;
  }

  .card-number {
    position: absolute; right: 36px; top: 30px;
    font-family: "Comic Neue", cursive; font-size: 18px; color: var(--ink);
  }
  .field {
    position: absolute; font-family: "Comic Neue", cursive; color: var(--ink);
    display: flex; align-items: flex-end;
  }
  .field .label { white-space: nowrap; }
  .field .line { border-bottom: 1.5px solid var(--rule); margin-bottom: 5px; }
  .field--large { font-size: 27px; font-weight: 700; }
  .field--small { font-size: 22px; }

  .mascot-art {
    position: absolute; left: 533px; top: 220px; width: 120px; height: 128px;
    border-radius: 8px;
    background: linear-gradient(160deg, var(--brand-blue) 0%, #5a5ae0 55%, var(--sun-yellow) 100%);
  }
</style>
</head>
<body>
<main class="canvas">
  <section class="card business-card">
    <h1 class="brand-name">TILLOW MARSH</h1>
    <div class="contact">
      <p>482 Larkfield Ave. Harlow Bay, MI 48791</p>
      <p><b>P:</b> 989.517.4296 &nbsp;<b>E:</b> Office@TillowMarsh.com</p>
      <p><b>W:</b> www.TillowMarsh.com</p>
    </div>
    <div class="offer-band">
      <p>Gourmet Food | Fine Wines | Gift Baskets</p>
      <p>Kitchen &amp; Bath Accessories | Candles | Cards | Soaps</p>
    </div>
  </section>

  <section class="card gift-card">
    <p class="card-number">Card Number : 58724</p>

    <div class="field field--large" style="left:58px; top:84px;">
      <span class="label">To :</span><span class="line" style="width:541px; margin-left:20px;"></span>
    </div>
    <div class="field field--large" style="left:58px; top:142px;">
      <span class="label">Form :</span><span class="line" style="width:514px; margin-left:12px;"></span>
    </div>
    <div class="field field--small" style="left:55px; top:227px;">
      <span class="label">Date &nbsp;Issued :</span><span class="line" style="width:305px; margin-left:8px;"></span>
    </div>
    <div class="field field--small" style="left:55px; top:275px;">
      <span class="label">Expiration Date :</span><span class="line" style="width:275px; margin-left:8px;"></span>
    </div>
    <div class="field field--small" style="left:55px; top:323px;">
      <span class="label">Employee :</span><span class="line" style="width:325px; margin-left:28px;"></span>
    </div>

    <div class="mascot-art" role="img" aria-label="Blue dancing figure stepping over a yellow rising sun"></div>
  </section>
</main>
</body>
</html>
```